Fast-casual chicken restaurant Crisp Harbor needs a catering menu design

We need a catering menu designed for Crisp Harbor. We are looking to design a 24x36in landscape menu board for our new catering menu. The catering memo attached includes our catering menu and Crisp Harbor branding. More information about our brand can be found at https://crispharbor-eats.example/.

```html
<!DOCTYPE html>
<html lang="en">
<head>
<meta charset="utf-8">
<title>Crisp Harbor Catering Menu Board</title>
<link href="https://fonts.googleapis.com/css2?family=Montserrat:wght@700;800;900&display=swap" rel="stylesheet">
<style>
  :root{
    --page:#f4f1ec;
    --wood-dark:#2a1208;
    --wood:#4a2412;
    --wood-mid:#5e2f17;
    --gold:#f2c230;
    --gold-deep:#d9a91f;
    --red:#d8392a;
    --slate:#5d6166;
    --ink:#111;
    --white:#fff;
    --concrete:#c9c9c6;
    --chicken:#c8461c;
  }
  *{box-sizing:border-box;margin:0;padding:0}
  html,body{width:957px;height:1200px;overflow:hidden;background:var(--page)}
  body{font-family:"Montserrat",Arial,sans-serif;color:var(--white);position:relative}

  .menu-board{
    position:absolute;left:0;top:281px;width:957px;height:638px;overflow:hidden;
    background:
      radial-gradient(ellipse at 50% 40%,rgba(120,60,25,.35),transparent 70%),
      repeating-linear-gradient(90deg,var(--wood) 0 14px,var(--wood-mid) 14px 17px,var(--wood) 17px 40px,#3c1c0d 40px 43px),
      var(--wood);
  }

  /* ---------- deal blocks ---------- */
  .deal{position:absolute;top:14px;width:450px;height:176px;border:2px solid var(--gold);border-top:none}
  .deal--packaged{left:19px}
  .deal--per-person{left:490px}
  .deal__banner{position:relative;height:72px;display:flex}
  .deal__photo{flex:1;background:linear-gradient(135deg,#d9d7d2,var(--chicken) 55%,#8a2a10)}
  .deal__photo--right{background:linear-gradient(225deg,#cfcdc8,var(--chicken) 55%,#7d2610)}
  .deal__title{
    width:206px;background:var(--wood-dark);border:2px solid var(--gold);border-bottom:none;
    color:var(--gold);font-weight:900;font-size:26px;line-height:26px;text-align:center;
    display:flex;align-items:center;justify-content:center;padding-top:2px;
  }
  .deal--per-person .deal__title{font-size:25px}

  .deal-table{width:100%;border-collapse:collapse;table-layout:fixed}
  .deal-table th{
    background:var(--slate);height:24px;font-weight:800;font-size:14px;text-align:left;padding-left:7px;
    border-right:2px solid var(--gold);border-top:2px solid var(--gold);
  }
  .deal-table th.c{text-align:center;padding:0}
  .deal-table td{
    height:26px;border-right:2px solid var(--gold);border-top:1px solid rgba(242,194,48,.25);
    background:rgba(30,12,5,.45);font-weight:800;vertical-align:middle;
  }
  .deal-table th:last-child,.deal-table td:last-child{border-right:none}
  .deal-table .name{font-size:9px;padding-left:10px;line-height:10px}
  .deal-table .name small{display:block;font-size:5px;line-height:6px}
  .deal-table .feeds{text-align:center;font-size:13px}
  .deal-table .items{font-size:8.5px;line-height:10px;padding-left:10px}
  .deal-table .price{text-align:center;font-size:14px}
  .deal--per-person .name{text-align:center;padding-left:0}

  /* ---------- a la carte ---------- */
  .carte{position:absolute;left:19px;top:207px;width:921px;height:216px;overflow:hidden;
    background:linear-gradient(90deg,#b5b3ae,var(--concrete) 30%,#d2d1ce 70%,#b9b7b2)}
  .carte__photo{position:absolute;top:0;height:216px;width:240px}
  .carte__photo--left{left:0;background:radial-gradient(ellipse at 40% 45%,var(--chicken) 0 45%,#e8e6e1 62%,transparent 75%)}
  .carte__photo--right{right:0;background:radial-gradient(ellipse at 60% 50%,var(--chicken) 0 45%,#e8e6e1 62%,transparent 75%)}
  .carte__header{position:absolute;left:240px;top:0;width:440px;height:33px;background:var(--red);
    font-weight:900;font-size:28px;text-align:center;line-height:35px}
  .carte-table{position:absolute;left:240px;top:33px;width:440px;height:183px;border-collapse:collapse;table-layout:fixed;
    background:linear-gradient(90deg,#e3e1dc 0%,#e9c64a 30%,var(--gold) 55%,#f1cf58 85%,rgba(240,214,120,.2) 100%)}
  .carte-table th{background:var(--ink);color:var(--gold);font-weight:800;font-size:13px;height:19px;text-align:left;padding-left:12px;border-right:1px solid var(--gold-deep)}
  .carte-table th:nth-child(2){text-align:center;padding:0}
  .carte-table td{color:var(--ink);font-weight:800;font-size:14px;height:19.5px;line-height:19px;padding-left:12px;border-right:1px solid rgba(60,40,0,.35)}
  .carte-table td:nth-child(2){padding-left:27px}
  .carte-table th:last-child,.carte-table td:last-child{border-right:none;padding-left:26px}
  .carte-table tbody tr:first-child td{padding-top:5px}

  /* ---------- flavor columns ---------- */
  .flavors{position:absolute;left:19px;top:435px;width:921px;height:203px;display:flex;gap:9px}
  .flavor-col{flex:1;border:2px solid var(--gold);border-bottom:none;background:rgba(25,10,4,.55)}
  .flavor-col--red{border-color:var(--red)}
  .flavor-col__title{height:34px;color:var(--gold);font-weight:900;font-size:22px;text-align:center;line-height:36px;border-bottom:2px solid var(--gold)}
  .flavor-col--red .flavor-col__title{color:var(--red);border-bottom-color:var(--red)}
  .flavor-col ul{list-style:none;padding-top:8px}
  .flavor-col li{font-weight:800;font-size:13px;line-height:14px;text-align:center;height:28px;padding-top:4px}
</style>
</head>
<body>
<main class="menu-board">

  <section class="deal deal--packaged">
    <div class="deal__banner">
      <div class="deal__photo" role="img" aria-label="Tenders, wings and waffle fries on a platter"></div>
      <h2 class="deal__title">PACKAGED<br>DEALS</h2>
      <div class="deal__photo deal__photo--right" role="img" aria-label="Tray of sauced chicken wings"></div>
    </div>
    <table class="deal-table">
      <colgroup><col style="width:68px"><col style="width:71px"><col style="width:241px"><col></colgroup>
      <thead><tr><th class="c">NAME</th><th class="c">FEEDS</th><th>ITEMS</th><th class="c">PRICE</th></tr></thead>
      <tbody>
        <tr><td class="name">FAMILY</td><td class="feeds">4</td><td class="items">12 tenders, Sauces, Dressing, Large side, 2L</td><td class="price">$24.99</td></tr>
        <tr><td class="name">TAILGATE</td><td class="feeds">10</td><td class="items">20 Tenders, 30 Wings, Sauces, Dressings,<br>1 Party side</td><td class="price">$75.99</td></tr>
        <tr><td class="name">HOUSE<br>PARTY</td><td class="feeds">10</td><td class="items">20 Tenders, 60 Wings, Sauces, 2 Party sides,<br>2 Party Salads, Dressings, 2 2L</td><td class="price">$155.99</td></tr>
      </tbody>
    </table>
  </section>

  <section class="deal deal--per-person">
    <div class="deal__banner">
      <div class="deal__photo" role="img" aria-label="Spread of wings, fries and onion rings"></div>
      <h2 class="deal__title">PER PERSON<br>DEALS</h2>
      <div class="deal__photo deal__photo--right" role="img" aria-label="Plate of dry rub wings"></div>
    </div>
    <table class="deal-table">
      <colgroup><col style="width:70px"><col style="width:69px"><col style="width:241px"><col></colgroup>
      <thead><tr><th class="c">NAME</th><th class="c">FEEDS</th><th>ITEMS</th><th class="c">PRICE</th></tr></thead>
      <tbody>
        <tr><td class="name">SNACK<small>(PER PERSON)</small></td><td class="feeds">1</td><td class="items">2 tenders, Sauce, Dressing, 1 reg side</td><td class="price">$7.99</td></tr>
        <tr><td class="name">PARTY<small>(PER PERSON)</small></td><td class="feeds">1</td><td class="items">2 Tenders, 3 Wings, Sauce, Dressing, 1 reg side, 12oz/fountain drink</td><td class="price">$11.99</td></tr>
        <tr><td class="name">FEAST<small>(PER PERSON)</small></td><td class="feeds">1</td><td class="items">2 Tenders, 6 Wings, Sauce, Dressing, 1 reg side, Dessert, 20 oz drink</td><td class="price">$15.99</td></tr>
      </tbody>
    </table>
  </section>

  <section class="carte">
    <div class="carte__photo carte__photo--left" role="img" aria-label="Plate of sauced chicken tenders"></div>
    <div class="carte__photo carte__photo--right" role="img" aria-label="Plate of sauced tenders with dipping sauce"></div>
    <h2 class="carte__header">A LA CARTE</h2>
    <table class="carte-table">
      <colgroup><col style="width:187px"><col style="width:134px"><col></colgroup>
      <thead><tr><th>ITEMS</th><th>INCREMENTS</th><th>PRICE</th></tr></thead>
      <tbody>
        <tr><td>Wings</td><td>50, 75, 100</td><td>$xx.xx</td></tr>
        <tr><td>Tenders</td><td>30, 45, 60</td><td>$xx.xx</td></tr>
        <tr><td>Waffle Fries</td><td>Party Size</td><td>$13.99</td></tr>
        <tr><td>Garlic Pram Tots</td><td>Party Size</td><td>$13.99</td></tr>
        <tr><td>Chicken Caesar Salad</td><td>Party Size</td><td>$38.99</td></tr>
        <tr><td>Caesar Salad</td><td>Party Size</td><td>$27.99</td></tr>
        <tr><td>Any Sauce</td><td>8 oz</td><td>$1.99</td></tr>
        <tr><td>Cheese Sauce</td><td>8 oz</td><td>$2.49</td></tr>
      </tbody>
    </table>
  </section>

  <section class="flavors">
    <div class="flavor-col"><h3 class="flavor-col__title">FLAVORS</h3>
      <ul><li>HONEY MUSTARD</li><li>HOT LEMON PEPPER</li><li>JAMAICAN JERK</li><li>MANGO HABANERO</li><li>SWEET CHILI</li></ul></div>
    <div class="flavor-col flavor-col--red"><h3 class="flavor-col__title">BBQ</h3>
      <ul><li>CAJUN BBQ</li><li>CITRUS CHIPOTLE</li><li>GOLDEN BBQ</li><li>HONEY BBQ</li><li>KICKIN BBQ</li></ul></div>
    <div class="flavor-col"><h3 class="flavor-col__title">DRY RUBS</h3>
      <ul><li>7 PEPPER</li><li>CAJUN</li><li>GARLIC PARM</li><li>LEMON PEPPER</li><li>WEST TEXAS<br>MESQUITE</li></ul></div>
    <div class="flavor-col flavor-col--red"><h3 class="flavor-col__title">TERIYAKI</h3>
      <ul><li>CAJUN TERIYAKI</li><li>SPICY TERIYAKI</li><li>TRADITIONAL<br>TERIYAKI</li></ul></div>
    <div class="flavor-col"><h3 class="flavor-col__title">BUFFALO</h3>
      <ul><li>CALM WATERS</li><li>ROLLING HIGH TIDE</li><li>RED BUOY</li><li>STORM SURGE</li><li>RIPTIDE</li></ul></div>
  </section>

</main>
</body>
</html>
```